High-end Oceanfront Real Estate Group Needs Clean, Modern Web Design

I’m looking for a clean, professional, modern and beautiful homepage web design for a Real Estate group in Southern California, USA.

The group/company is “Marwick on the Shore,” and they specialize in high end (i.e. expensive), oceanfront real estate in the Orange County area.

The look and feel of the page should accentuate the brand qualities: luxurious/expensive, professional, and beautiful (Orange County is one of the most beautiful areas in all the US and we would love the site to emphasize the beautiful beaches and scenery it has to offer).

Looks we like:
• www.brantleyhomesrealty.example
• www.closedbyvane.example -- I think the design is pretty out-dated in this site, but I like the organization/layout of the site

Header Tags (I don’t know if we can fit all of these, may need a side-menu, but I’d prefer header title only if possible):
• Welcome
• Featured Listings
• Previously Sold
• Sell
• Property Search
• Team
• Videos
• Blog
• Explore O.C.
• Contact

I have attached the beach and logo pics that we would like to use as the header, a few pictures of the team, and one sample home/view pic which can be used in any of the other sections (for pictures of the homes, just find expensive oceanfront houses and that will be fine).

I promise to provide feedback to each and every design submission. I appreciate the hard work that all of you are putting into your designs. There can be only one contest winner, but I hope to give all of you helpful feedback to submit the best designs possible!

Target Market(s)

Very wealthy home owners of oceanfront properties. These properties are worth several millions of dollars, and thus the site and brand needs to be targeted to very wealthy, successful individuals and families (both US and international buyers).

Industry/Entity Type

Real Estate

Number of Pages Required

2 page

Requirements
Must have
• I don’t want to give too many requirements, because I want to let you all be creative. However, here are the few Must Haves:
• Must submit 2 page designs (a home page and a sub page)
• Must use logo provided
• Focus is mostly on homes, but I would like to include some beach/ocean imagery as well
• The first “item” on the home page should be an accordion/slider which shows pictures of homes and with 1 line of text: “List with the Leader” and two link buttons: “Sell Your Home” and “Buy Your Home”
• Color palette needs to be mainly blues--to match ocean and sky blue
• Exported in all major formats (psd,ai,eps,png,jpeg,etc)
Nice to have
• We don’t necessarily need all of these, but would like to feature most:
• List of videos
• “Meet the Team”—brief team bios and pics
• Link(s) to Blog
• “List with the Leader” – section on why they should choose this firm
• Featured Listings
• Previously Sold

```html
<!DOCTYPE html>
<html lang="en">
<head>
<meta charset="utf-8">
<title>Marwick on the Shore — Home</title>
<link href="https://fonts.googleapis.com/css2?family=Open+Sans:wght@400;600;700&display=swap" rel="stylesheet">
<style>
:root{
  --blue:#2346b8;
  --blue-dark:#1b3590;
  --blue-deep:#16307f;
  --sky:#1d4fa8;
  --ink:#333a45;
  --muted:#7a808a;
  --line:#e2e4e8;
  --white:#ffffff;
  --dark:#22261f;
}
*{box-sizing:border-box;margin:0;padding:0}
html,body{width:1200px;height:3125px;overflow:hidden}
body{font-family:"Open Sans",Arial,sans-serif;color:var(--ink);background:var(--white);position:relative}
.abs{position:absolute}

/* hero */
.hero{left:0;top:0;width:1200px;height:694px;background:linear-gradient(180deg,#0d3a94 0%,#1f5fc0 45%,#6b86a8 70%,#5a5040 100%)}
.hero-photo{position:absolute;inset:0;background:
  radial-gradient(ellipse 200px 420px at 1140px 330px,#c2431a 0%,rgba(194,67,26,0) 100%),
  linear-gradient(180deg,rgba(0,0,0,0) 40%,rgba(150,130,95,.55) 62%,rgba(60,70,40,.7) 100%)}
.brand{left:496px;top:58px;width:112px;height:112px;background:rgba(205,220,235,.85);display:flex;align-items:center;justify-content:center;text-align:center;color:var(--blue-deep);font-size:17px;font-weight:600;line-height:1.2;padding:8px}
.hero-arrow{top:345px;width:20px;height:28px}
.hero-panel{left:356px;top:315px;width:471px;height:127px;background:rgba(230,236,245,.88);text-align:center;padding-top:26px}
.hero-panel h1{font-size:25px;font-weight:400;color:var(--blue)}
.hero-actions{display:flex;justify-content:center;gap:16px;margin-top:18px}
.btn{display:inline-block;font-size:14px;height:34px;line-height:32px;padding:0 30px}
.btn-solid{background:var(--blue);color:var(--white);border:1px solid var(--blue)}
.btn-ghost{background:var(--white);color:var(--blue);border:1px solid var(--blue)}

/* nav */
.nav{left:0;top:694px;width:1200px;height:58px;background:var(--blue);display:flex;padding-left:58px}
.nav a{color:var(--white);font-size:13px;font-weight:600;text-decoration:none;line-height:58px;padding:0 20px}
.nav a.active{background:var(--blue-dark);padding:0 28px}

/* about */
.about-head{left:58px;top:860px;width:330px}
.about-head h2{font-size:29px;font-weight:600;color:var(--blue)}
.about-head p{font-size:16px;color:var(--muted);margin-top:6px;line-height:1.5}
.about-rule{left:433px;top:818px;width:1px;height:150px;background:var(--line)}
.about-tick{left:432px;top:874px;width:3px;height:50px;background:var(--blue)}
.about-body{left:496px;top:834px;width:620px;font-size:13px;line-height:1.7;color:var(--muted)}
.about-body .btn{margin-top:16px;font-size:12px;height:30px;line-height:28px;padding:0 24px}

/* section titles */
.section-title{left:0;width:1200px;text-align:center;font-size:27px;font-weight:600;color:var(--blue)}
.section-title.left{left:58px;width:auto;text-align:left}

/* videos */
.videos{left:60px;top:1115px;display:flex;gap:31px}
.thumb{width:246px;height:160px;border:2px solid #d8dbe0}
.side-arrow{top:1185px;width:14px;height:22px}

/* blog band */
.blog-band{left:58px;top:1327px;width:1084px;height:81px;background:var(--blue);display:flex;align-items:center;justify-content:space-between;padding:0 33px}
.blog-band p{color:var(--white);font-size:17px;font-weight:600}
.blog-band .btn{background:var(--blue-deep);color:#c7d2f0;font-size:16px;width:226px;height:40px;line-height:40px;text-align:center;padding:0;margin-right:0}

/* team */
.team{left:60px;top:1531px;display:flex;gap:19px}
.member{width:201px;height:317px;border:1px solid var(--line);border-bottom:3px solid var(--blue);text-align:center}
.member h3{font-size:12px;font-weight:700;margin-top:10px;color:#222}
.member .role{font-size:10px;color:var(--blue);margin-top:2px}
.member .portrait{width:199px;height:222px;margin-top:10px}
.member .social{display:flex;justify-content:center;gap:16px;padding-top:10px}
.member .social span{width:12px;height:12px;border-radius:50%;background:#2a3040}

/* pitch */
.pitch{left:0;top:1898px;width:1200px;height:367px;background:radial-gradient(ellipse 500px 260px at 600px 200px,#4d5a3a 0%,#2b3021 60%,#1d2018 100%);color:var(--white);text-align:center;padding-top:28px}
.pitch h2{font-size:27px;font-weight:600}
.pitch p{width:1070px;margin:18px auto 0;font-size:12px;line-height:1.8}
.pitch ul{width:380px;margin:18px auto 0;text-align:left;list-style:none;font-size:12px;line-height:2.3}
.pitch li::before{content:"";display:inline-block;width:7px;height:7px;border-radius:50%;background:var(--white);margin-right:16px;vertical-align:middle}
.pitch .btn{margin-top:12px;font-size:14px;padding:0 44px}

/* carousel arrows */
.pager{display:flex;gap:4px}
.pager span{width:19px;height:19px;border-radius:50%;border:1.5px solid var(--blue);display:flex;align-items:center;justify-content:center}
.pager span.on{background:var(--blue)}

/* listings */
.listings{left:60px;top:2381px;display:flex;gap:11px}
.listing{width:264px;text-align:center}
.listing .photo{width:264px;height:162px}
.listing .caption{font-size:12px;color:var(--muted);line-height:1.5;margin-top:16px;padding:0 6px}
.listing .price{font-size:17px;color:var(--ink);margin-top:8px}
.specs{display:flex;justify-content:space-between;margin-top:14px;border-bottom:1px solid var(--line);padding:0 12px 8px}
.spec{font-size:10px;color:var(--muted);width:60px;display:flex;flex-direction:column;align-items:center;gap:3px}
.spec.on{color:var(--blue)}

/* sold */
.sold{left:60px;top:2794px;display:flex;gap:16px}
.sold-item{width:203px;text-align:center}
.sold-item .photo{width:203px;height:133px}
.sold-item p{font-size:16px;font-weight:600;color:#444;margin-top:13px}

/* footer */
.footer{left:0;top:3031px;width:1200px;height:94px;background:var(--blue);color:var(--white)}
.footer-links{position:absolute;top:19px;width:1200px;text-align:center;font-size:12px}
.footer-links a{color:var(--white);text-decoration:none;padding:0 8px}
.footer-copy{position:absolute;left:58px;top:64px;font-size:11px}
.footer-page{position:absolute;right:38px;top:22px;font-size:12px}
.footer-social{position:absolute;right:32px;top:60px;display:flex;gap:10px}
.footer-social span{width:20px;height:20px;border-radius:50%;background:var(--white)}
</style>
</head>
<body>

<header class="abs hero">
  <div class="hero-photo" role="img" aria-label="Two-storey family home under a clear blue sky with an autumn tree"></div>
  <div class="abs brand">Marwick on the Shore</div>
  <svg class="abs hero-arrow" style="left:40px" viewBox="0 0 20 28"><path d="M14 4 5 14l9 10" fill="none" stroke="#fff" stroke-width="2"/></svg>
  <svg class="abs hero-arrow" style="left:1140px" viewBox="0 0 20 28"><path d="M6 4l9 10-9 10" fill="none" stroke="#fff" stroke-width="2"/></svg>
  <div class="abs hero-panel">
    <h1>List with the Leader</h1>
    <div class="hero-actions">
      <a class="btn btn-solid" style="width:176px">Sell Your Home</a>
      <a class="btn btn-ghost" style="width:176px">Buy Your Home</a>
    </div>
  </div>
</header>

<nav class="abs nav">
  <a class="active">Welcome</a><a>Featured Listings</a><a>Previously Sold</a><a>Sell</a><a>Property Search</a><a>Team</a><a>Videos</a><a>Blog</a><a>Explore O.C</a><a>Contact</a>
</nav>

<section>
  <div class="abs about-head">
    <h2>About Us</h2>
    <p>Lorem ipsum dolor sit amet, consectetur adipiscing elit. mollis.</p>
  </div>
  <div class="abs about-rule"></div>
  <div class="abs about-tick"></div>
  <div class="abs about-body">
    <p>We at Marwick on the Shore are privileged to help people from all over the world find their dream homes in Monarch Beach, Laguna Beach, Newport Coast, Dana Point, San Clemente and San Juan Capistrano. Whether you are buying or selling a property in Orange County, we want to help you in the most efficient, professional way possible.</p>
    <a class="btn btn-solid">Read More</a>
  </div>
</section>

<h2 class="abs section-title" style="top:1054px">Our Videos</h2>
<svg class="abs side-arrow" style="left:16px" viewBox="0 0 14 22"><path d="M11 2 3 11l8 9" fill="none" stroke="#bbb" stroke-width="1.5"/></svg>
<svg class="abs side-arrow" style="left:1166px" viewBox="0 0 14 22"><path d="M3 2l8 9-8 9" fill="none" stroke="#bbb" stroke-width="1.5"/></svg>
<div class="abs videos">
  <div class="thumb" role="img" aria-label="Video: beach with lifeguard tower" style="background:linear-gradient(180deg,#3c84c8 0%,#7bb0d8 50%,#d8ccb0 100%)"></div>
  <div class="thumb" role="img" aria-label="Video: large villa with lawn" style="background:linear-gradient(180deg,#5f97d6 0%,#c9b89a 55%,#5e8a3c 100%)"></div>
  <div class="thumb" role="img" aria-label="Video: brick house with garden" style="background:linear-gradient(180deg,#6aa2dc 0%,#9a4a32 50%,#4f8a32 100%)"></div>
  <div class="thumb" role="img" aria-label="Video: suburban street of houses" style="background:linear-gradient(180deg,#7eb2e4 0%,#b9c4cc 50%,#5f9040 100%)"></div>
</div>

<div class="abs blog-band">
  <p>Lorem ipsum dolor sit amet, consectetur adipiscing elit. Pellentesque nec vehicula orci.</p>
  <a class="btn">Check out our blog</a>
</div>

<h2 class="abs section-title" style="top:1462px">Meet the Team</h2>
<div class="abs team">
  <div class="member"><h3>GLEN</h3><p class="role">Lorem ipsum dol</p><div class="portrait" role="img" aria-label="Portrait of team member Glen" style="background:linear-gradient(180deg,#3a2a20,#7c6a58)"></div><div class="social"><span></span><span></span><span></span><span></span></div></div>
  <div class="member"><h3>NORA MARWICK</h3><p class="role">Contantry popilar</p><div class="portrait" role="img" aria-label="Portrait of team member Nora Marwick" style="background:linear-gradient(180deg,#7a8ea4,#c7ab8f)"></div><div class="social"><span></span><span></span><span></span><span></span></div></div>
  <div class="member"><h3>LENA ORTIZ</h3><p class="role">Popilar sit amit</p><div class="portrait" role="img" aria-label="Portrait of team member Lena Ortiz" style="background:linear-gradient(180deg,#9a9a96,#4a3a30)"></div><div class="social"><span></span><span></span><span></span><span></span></div></div>
  <div class="member"><h3>LENA ORTIZ</h3><p class="role">Ipsum dolor</p><div class="portrait" role="img" aria-label="Portrait of team member Lena Ortiz" style="background:linear-gradient(180deg,#d8a63a,#6a3a28)"></div><div class="social"><span></span><span></span><span></span><span></span></div></div>
  <div class="member"><h3>LENA ORTIZ</h3><p class="role">Lorem ipsum</p><div class="portrait" role="img" aria-label="Portrait of team member Lena Ortiz" style="background:linear-gradient(180deg,#b8343a,#5a2a50)"></div><div class="social"><span></span><span></span><span></span><span></span></div></div>
</div>

<section class="abs pitch" role="img" aria-label="Blurred garden path behind the section text">
  <h2>List with the Leader</h2>
  <p>Phasellus quis arcu eget arcu gravida rutrum a id nibh. Donec et sagittis neque, a efficitur ex. Sed placerat lobortis malesuada. Curabitur turpis eros, vehicula et nisi ac, dapibus tempus odio. Sed in lacus sollicitudin, pretium augue et, semper nisi. Class aptent taciti sociosqu ad litora torquent per conubia nostra, per inceptos himenaeos. Pellentesque at nisi at magna placerat ultricies sed sed ligula.</p>
  <ul>
    <li>Nam non magna pulvinar, ultrices nibh non, consequat</li>
    <li>quam. Maecenas vel enim eget augue convallis posuere et</li>
    <li>eu nibh. Vivamus gravida, quam eu rhoncus malesuada,</li>
    <li>quam tellus dictum lacus, in semper</li>
  </ul>
  <a class="btn btn-solid">Read More</a>
</section>

<h2 class="abs section-title left" style="top:2314px">Featured Listings</h2>
<div class="abs pager" style="left:1096px;top:2326px"><span><svg width="9" height="9" viewBox="0 0 9 9"><path d="M6 1 2 4.5 6 8" fill="none" stroke="#2346b8" stroke-width="1.5"/></svg></span><span class="on"><svg width="9" height="9" viewBox="0 0 9 9"><path d="M3 1l4 3.5L3 8" fill="none" stroke="#fff" stroke-width="1.5"/></svg></span></div>
<div class="abs listings">
  <div class="listing"><div class="photo" role="img" aria-label="Commercial building with lease sign" style="background:linear-gradient(180deg,#8fb4dc,#d4c6a8 60%,#b23030)"></div><p class="caption">Eelington hall, ribrry selvia homes, lorem ipsum dolor</p><p class="price">$3943.39</p><div class="specs"><div class="spec on"><svg width="12" height="14" viewBox="0 0 12 14"><path d="M6 13S1 8 1 5a5 5 0 0110 0c0 3-5 8-5 8z" fill="#2346b8"/></svg>Lorem ipdm</div><div class="spec"><svg width="16" height="12" viewBox="0 0 16 12"><path d="M1 1v10M1 7h14v4M4 7V4h6v3" fill="none" stroke="#999" stroke-width="1.3"/></svg>4 beds</div><div class="spec"><svg width="14" height="14" viewBox="0 0 14 14"><path d="M3 4a5 5 0 11-1 5M3 1v3h3" fill="none" stroke="#999" stroke-width="1.3"/></svg>m2</div></div></div>
  <div class="listing"><div class="photo" role="img" aria-label="Agent standing in a modern interior" style="background:linear-gradient(90deg,#9a5a30,#d8d4cc 55%,#8a8a88)"></div><p class="caption">Eelington hall, ribrry selvia homes, lorem ipsum dolor</p><p class="price">$3943.39</p><div class="specs"><div class="spec"><svg width="12" height="14" viewBox="0 0 12 14"><path d="M6 13S1 8 1 5a5 5 0 0110 0c0 3-5 8-5 8z" fill="none" stroke="#999" stroke-width="1.3"/></svg>Lorem ipdm</div><div class="spec"><svg width="16" height="12" viewBox="0 0 16 12"><path d="M1 1v10M1 7h14v4M4 7V4h6v3" fill="none" stroke="#999" stroke-width="1.3"/></svg>4 beds</div><div class="spec"><svg width="14" height="14" viewBox="0 0 14 14"><path d="M3 4a5 5 0 11-1 5M3 1v3h3" fill="none" stroke="#999" stroke-width="1.3"/></svg>m2</div></div></div>
  <div class="listing"><div class="photo" role="img" aria-label="Hand holding a small model house" style="background:linear-gradient(180deg,#3a3a3c,#b8b8b4 60%,#e6dcd0)"></div><p class="caption">Eelington hall, ribrry selvia homes, lorem ipsum dolor</p><p class="price">$3943.39</p><div class="specs"><div class="spec"><svg width="12" height="14" viewBox="0 0 12 14"><path d="M6 13S1 8 1 5a5 5 0 0110 0c0 3-5 8-5 8z" fill="none" stroke="#999" stroke-width="1.3"/></svg>Lorem ipdm</div><div class="spec"><svg width="16" height="12" viewBox="0 0 16 12"><path d="M1 1v10M1 7h14v4M4 7V4h6v3" fill="none" stroke="#999" stroke-width="1.3"/></svg>4 beds</div><div class="spec"><svg width="14" height="14" viewBox="0 0 14 14"><path d="M3 4a5 5 0 11-1 5M3 1v3h3" fill="none" stroke="#999" stroke-width="1.3"/></svg>m2</div></div></div>
  <div class="listing"><div class="photo" role="img" aria-label="Suburban house with front lawn" style="background:linear-gradient(180deg,#7aa8dc,#c2c0b8 55%,#5a8c3a)"></div><p class="caption">Eelington hall, ribrry selvia homes, lorem ipsum dolor</p><p class="price">$3943.39</p><div class="specs"><div class="spec"><svg width="12" height="14" viewBox="0 0 12 14"><path d="M6 13S1 8 1 5a5 5 0 0110 0c0 3-5 8-5 8z" fill="none" stroke="#999" stroke-width="1.3"/></svg>Lorem ipdm</div><div class="spec"><svg width="16" height="12" viewBox="0 0 16 12"><path d="M1 1v10M1 7h14v4M4 7V4h6v3" fill="none" stroke="#999" stroke-width="1.3"/></svg>4 beds</div><div class="spec"><svg width="14" height="14" viewBox="0 0 14 14"><path d="M3 4a5 5 0 11-1 5M3 1v3h3" fill="none" stroke="#999" stroke-width="1.3"/></svg>m2</div></div></div>
</div>

<h2 class="abs section-title left" style="top:2738px">Previously Sold</h2>
<div class="abs pager" style="left:1096px;top:2752px"><span><svg width="9" height="9" viewBox="0 0 9 9"><path d="M6 1 2 4.5 6 8" fill="none" stroke="#2346b8" stroke-width="1.5"/></svg></span><span class="on"><svg width="9" height="9" viewBox="0 0 9 9"><path d="M3 1l4 3.5L3 8" fill="none" stroke="#fff" stroke-width="1.5"/></svg></span></div>
<div class="abs sold">
  <div class="sold-item"><div class="photo" role="img" aria-label="Sold home with flowering garden" style="background:linear-gradient(180deg,#6a9ad8,#a88a6a 55%,#4a8a30)"></div><p>Lorme ipsum</p></div>
  <div class="sold-item"><div class="photo" role="img" aria-label="Sold single-storey home" style="background:linear-gradient(180deg,#4a82d0,#8a7a62 55%,#6a9040)"></div><p>Lorme ipsum</p></div>
  <div class="sold-item"><div class="photo" role="img" aria-label="Sold white colonial house" style="background:linear-gradient(180deg,#3a78d0,#d8d8d4 55%,#4a8030)"></div><p>Lorme ipsum</p></div>
  <div class="sold-item"><div class="photo" role="img" aria-label="Sold brick townhouses" style="background:linear-gradient(180deg,#8ab4e0,#a85a40 55%,#7a8a6a)"></div><p>Lorme ipsum</p></div>
  <div class="sold-item"><div class="photo" role="img" aria-label="Sold two-storey family home" style="background:linear-gradient(180deg,#5a90d8,#b8a482 55%,#5a8a38)"></div><p>Lorme ipsum</p></div>
</div>

<footer class="abs footer">
  <div class="footer-links"><a>Home</a>|<a>FAQ</a>|<a>Sitemap</a>|<a>Privacy Policy</a>|<a>Contact</a></div>
  <div class="footer-page">M3</div>
  <div class="footer-copy">© 2015 Yoursite, All rights reserved.</div>
  <div class="footer-social"><span></span><span></span><span></span></div>
</footer>

</body>
</html>
```